A clean crisp business card for a Landscape Construction company. Designed to be easy to read contact/ info and also be appealing/interesting, unlike a traditional business card.

Industry/Entity Type

Landscape Construction

Contact Information for Business Card

Company name : Brambleford Landscape Construction, phone number: (877) 62Vista, website:Bramblefordyards.example, Email, sales@bramblefordyards.example

Requirements
Nice to have
• Luxurious finishes/ details…. Icons or emblems next to contact info
Should not have
• Clipart or general pictures

```html
<!DOCTYPE html>
<html lang="en">
<head>
<meta charset="utf-8">
<title>Brambleford Landscape Construction – Business Card</title>
<link href="https://fonts.googleapis.com/css2?family=Montserrat:wght@500;600;700&family=Arimo:wght@400&display=swap" rel="stylesheet">
<style>
  :root {
    --stage: #2a2a2a;
    --card-dark: #050505;
    --card-light: #ffffff;
    --leaf-green: #8dc63f;
    --gear-blue: #1a6fc4;
    --ink: #222222;
  }
  * { box-sizing: border-box; margin: 0; padding: 0; }
  html, body {
    width: 1200px; height: 900px; overflow: hidden;
    background: var(--stage);
  }
  .canvas { position: relative; width: 1200px; height: 900px; }

  .card {
    position: absolute; width: 640px; height: 366px;
    box-shadow: 0 10px 30px rgba(0,0,0,.55);
  }

  /* Front: dark card with company name */
  .card-front {
    left: 130px; top: 60px;
    background: var(--card-dark);
    display: flex; align-items: center; justify-content: center; gap: 16px;
  }
  .brand-dot {
    width: 18px; height: 18px; border-radius: 50%;
    background: var(--leaf-green);
  }
  .brand-name {
    font-family: "Montserrat", sans-serif; font-weight: 600;
    font-size: 30px; letter-spacing: 1px; line-height: 1.25;
    color: var(--leaf-green); text-align: left;
  }

  /* Back: white contact card */
  .card-back {
    left: 430px; top: 474px;
    background: var(--card-light);
  }
  .person {
    position: absolute; right: 48px; top: 34px; text-align: right;
  }
  .person-name {
    font-family: "Montserrat", sans-serif; font-weight: 700;
    font-size: 26px; color: var(--leaf-green); line-height: 1;
  }
  .person-role {
    font-family: "Montserrat", sans-serif; font-weight: 500;
    font-size: 13px; color: var(--ink); letter-spacing: 1px; margin-top: 3px;
  }
  .contact-list {
    position: absolute; right: 32px; top: 110px;
    list-style: none;
    font-family: "Arimo", sans-serif; font-size: 12.5px; color: var(--ink);
    text-align: right; line-height: 1.35;
  }
  .contact-item {
    display: flex; justify-content: flex-end; align-items: flex-start; gap: 10px;
    margin-bottom: 4px;
  }
  .contact-item.address { margin-bottom: 14px; }
  .contact-icon { width: 14px; height: 14px; flex: none; margin-top: 1px; }
  .back-brand {
    position: absolute; left: 40px; bottom: 34px;
    display: flex; align-items: center; gap: 10px;
  }
  .back-brand .brand-name { font-size: 18px; }
  .back-brand .brand-dot { width: 12px; height: 12px; }
</style>
</head>
<body>
<main class="canvas">

  <section class="card card-front" aria-label="Card front">
    <span class="brand-dot" aria-hidden="true"></span>
    <h1 class="brand-name">Brambleford<br>Landscape Construction</h1>
  </section>

  <section class="card card-back" aria-label="Card back">
    <div class="person">
      <p class="person-name">Owen Castellane</p>
      <p class="person-role">CEO</p>
    </div>

    <ul class="contact-list">
      <li class="contact-item address">
        <span>4410 Orchard Hollow Rd.,<br>NUM 118, Fairbrook, OH 45990</span>
        <svg class="contact-icon" viewBox="0 0 16 16" aria-hidden="true">
          <path d="M8 1a5 5 0 0 0-5 5c0 4 5 9 5 9s5-5 5-9a5 5 0 0 0-5-5zm0 7a2 2 0 1 1 0-4 2 2 0 0 1 0 4z" fill="var(--leaf-green)"/>
        </svg>
      </li>
      <li class="contact-item">
        <span>(877) 62Vista</span>
        <svg class="contact-icon" viewBox="0 0 16 16" aria-hidden="true">
          <circle cx="8" cy="8" r="7" fill="none" stroke="var(--leaf-green)" stroke-width="1.4"/>
          <path d="M5.5 4.5l1.3 0 .6 1.8-.9.7a5 5 0 0 0 2.5 2.5l.7-.9 1.8.6v1.3c-3.5.3-6.3-2.5-6-6z" fill="var(--leaf-green)"/>
        </svg>
      </li>
      <li class="contact-item">
        <span>sales@bramblefordyards.example</span>
        <svg class="contact-icon" viewBox="0 0 16 16" aria-hidden="true">
          <rect x="1" y="3.5" width="14" height="9" fill="var(--leaf-green)"/>
          <path d="M1 3.5l7 5 7-5" fill="none" stroke="#fff" stroke-width="1.2"/>
        </svg>
      </li>
      <li class="contact-item">
        <span>www.bramblefordyards.example</span>
        <svg class="contact-icon" viewBox="0 0 16 16" aria-hidden="true">
          <circle cx="8" cy="8" r="7" fill="var(--leaf-green)"/>
          <path d="M1 8h14M8 1c-3 3.5-3 10.5 0 14M8 1c3 3.5 3 10.5 0 14" fill="none" stroke="#fff" stroke-width="1"/>
        </svg>
      </li>
    </ul>

    <div class="back-brand">
      <span class="brand-dot" aria-hidden="true"></span>
      <p class="brand-name">Brambleford Landscape Construction</p>
    </div>
  </section>

</main>
</body>
</html>
```